Design and Renovation Company Luxury Business Card

I want to create a luxury business card for a Design and Renovation Firm . We will use our current logo. The company name is 528BUILDA. We do not want anything standard. We need a very unique concept.
Please see uploaded inspiration. I really like the textured paper option. I would like the card to be thick with debossing, and/or embossing options. The logo has orange in it but I would like to see the card with and without the orange. I think the orange may make the company feel less high-end. The goal is to elevate the logo not match its vibe per se of the logo. We want something very unique, not standard at all!
I would like a space for :
Logo,
Name,
Position,
Email,
Office number,
Website Address,
Business Address,
Thank you!
Have fun!
Target Market(s)
Home owners Age 35 +
Industry/Entity Type
Design and Renovation
Contact Information for Business Card
Logo, Name, Position, Email, Office number, Website Address, Business Address,.
Colors
Designer to choose colors to be used in the design.
Requirements
Must have
- A luxury designer feel. Must be black or dark grey but open to other luxury ideas.
Nice to have
- Gold, silver, black embossing or debossing. Textured paper design.
Should not have
- A cheap look and feel.

```html
<!DOCTYPE html>
<html lang="en">
<head>
<meta charset="utf-8">
<title>528BUILDA Business Card</title>
<link rel="stylesheet" href="https://fonts.googleapis.com/css2?family=Arimo:wght@400;700&display=swap">
<style>
  :root {
    --backdrop: #9c9c9c;
    --card-contact: #3b3b3b;
    --card-brand: #2c2c2c;
    --accent: #f39c2b;
    --paper-white: #f4f4f4;
    --text-light: #e9e9e9;
  }
  * { margin: 0; padding: 0; box-sizing: border-box; }
  html, body { width: 1200px; height: 1050px; overflow: hidden; }
  body {
    background: var(--backdrop);
    font-family: "Arimo", Arial, sans-serif;
    position: relative;
  }
  .card {
    position: absolute;
    width: 760px;
    height: 430px;
    border-radius: 26px;
    overflow: hidden;
  }
  .card--contact {
    left: 110px; top: 70px;
    background: radial-gradient(circle at 30% 30%, #424242, var(--card-contact) 70%);
  }
  .card--brand {
    left: 330px; top: 550px;
    background: var(--card-brand);
  }
  .contact-mark {
    position: absolute;
    left: 70px; top: 60px;
    width: 78px; height: 78px;
    background: var(--accent);
  }
  .contact-block {
    position: absolute;
    left: 430px; top: 392px;
    width: 300px;
    height: 300px;
    transform: rotate(-90deg);
    transform-origin: top left;
    color: var(--text-light);
    font-size: 16px;
    line-height: 1.3;
  }
  .person-name {
    color: var(--accent);
    font-weight: 700;
    font-size: 24px;
    line-height: 1.1;
  }
  .person-role { font-size: 16px; }
  .divider {
    width: 38px;
    height: 1.5px;
    background: var(--text-light);
    margin: 20px 0 22px;
  }
  .contact-line {
    display: flex;
    align-items: center;
    gap: 8px;
  }
  .contact-line svg { width: 12px; height: 12px; flex: none; }
  .brand-lockup {
    position: absolute;
    left: 50%; top: 50%;
    transform: translate(-50%, -50%);
    display: flex;
    flex-direction: column;
    align-items: flex-start;
  }
  .brand-name-row {
    display: flex;
    align-items: center;
    gap: 16px;
  }
  .brand-square {
    width: 42px; height: 42px;
    background: var(--accent);
  }
  .brand-name {
    color: var(--paper-white);
    font-weight: 700;
    font-size: 72px;
    letter-spacing: 4px;
    line-height: 1;
  }
  .brand-tagline {
    margin: 8px 0 0 58px;
    color: var(--paper-white);
    font-weight: 700;
    font-size: 17px;
    letter-spacing: 7px;
  }
</style>
</head>
<body>

<section class="card card--contact" aria-label="Business card, contact side">
  <div class="contact-mark"></div>
  <div class="contact-block">
    <p class="person-name">Marcus Hale</p>
    <p class="person-role">President</p>
    <div class="divider"></div>
    <p>4120 Alder Crest Lane</p>
    <p>Ridgeview, NY 10562</p>
    <div class="divider"></div>
    <p class="contact-line">
      <svg viewBox="0 0 12 12" aria-hidden="true"><path d="M3 1 L5 3.5 L4 4.8 Q5.2 7 7.2 8 L8.5 7 L11 9 L9.8 11 Q5 11 1 3 Z" fill="var(--accent)"/></svg>
      (555) 0142-7788
    </p>
    <p class="contact-line">
      <svg viewBox="0 0 12 12" aria-hidden="true"><rect x="1" y="2.5" width="10" height="7" fill="var(--accent)"/><path d="M1 2.5 L6 6.5 L11 2.5" stroke="#3b3b3b" stroke-width="1" fill="none"/></svg>
      name@528BUILDA.com
    </p>
    <p class="contact-line">
      <svg viewBox="0 0 12 12" aria-hidden="true"><circle cx="6" cy="6" r="5" fill="var(--accent)"/><path d="M1 6 H11 M6 1 Q3 6 6 11 M6 1 Q9 6 6 11" stroke="#3b3b3b" stroke-width=".8" fill="none"/></svg>
      www.528BUILDA.com
    </p>
  </div>
</section>

<section class="card card--brand" aria-label="Business card, brand side">
  <div class="brand-lockup">
    <div class="brand-name-row">
      <div class="brand-square"></div>
      <span class="brand-name">528BUILDA</span>
    </div>
    <p class="brand-tagline">Design and Renovation Firm</p>
  </div>
</section>

</body>
</html>
```